Website Performance Testing eBook for the software testing industry

Overview:
I would like an ebook/whitepaper designed. This ebook will be digital published on my website as a lead generation piece. The purpose is to give high level tips on what to look for and things to think about when working on a website performance testing project.
The ebook also demonstrates our expertise and knowledge on the topic.
Topic:
This is an ebook on software testing. Specifically, website performance testing.
About Veltrana:
Veltrana Solutions is an outsourcing development and software testing firm, and we provide expert services for application development, testing and data analytics. We extend our clients’ software testing capabilities with on-demand technical expertise. Our quality assurance resources work as part of our clients’ teams to help test applications on time and within budget.
Our model is designed to allocate the right mix of local and offshore resources in order to optimize expertise, speed and cost. We provide the ability to quickly add specialty skills to our client’s development team without them incurring long-term costs. The result is far better management of resource capacities and outcomes.
Background on our branding and previous pieces:
I have included a few of our previous ebooks and whitepapers. I like the look and feel of these pieces, however we have made updates to our brand guidelines since them, so the new brand guidelines will need to be incorporated, and I'd like to refresh/update what we have done in the past.
Refer to our website for an idea of our look and feel. This page is one of our newer sections and would be a good reference:
http://www.veltranasol.example/data-analytics/
Tone and feel:
- The look and feel should be professional, clean and polished.
- I like good use of whitespace.
- I would prefer to keep stock photography of people to a minimum. Any images should add to the content and be relevant to the content.
(Also, I uploaded some InDesign files in case you wanted to refer to those assets, but I didn't include the Links folder because they were too big. If there's anything you more you need, let me know)
Target Market(s)
Audience:
The audience is senior Quality Assurance and Software Testing professionals.
- 30-45 years old
- Technical mindset
- Interested in learning
Titles include
- QA Lead
- QA Manager
- QA Director
- Director or VP of Development
- QA Automation Engineer
Our customers are medium to large sized companies. Many are software companies, but many are also enterprises in all almost all industries.

```html
<!DOCTYPE html>
<html lang="en">
<head>
<meta charset="utf-8">
<title>Website Performance Testing – Don't</title>
<link rel="stylesheet" href="https://fonts.googleapis.com/css2?family=Open+Sans:wght@300;400;600;700&display=swap">
<style>
  :root {
    --brand-red: #f04a37;
    --text-grey: #5a5a5a;
    --heading-dark: #1e1e1e;
    --rule-grey: #d4d4d4;
    --page-bg: #ffffff;
    --band-dark: #3d3a3a;
    --band-mid: #8a6456;
    --band-red: #d2473a;
  }
  * { margin: 0; padding: 0; box-sizing: border-box; }
  html, body { width: 927px; height: 1200px; overflow: hidden; background: var(--page-bg); }
  body { font-family: "Open Sans", sans-serif; color: var(--text-grey); position: relative; }

  .page-header {
    position: absolute; left: 54px; top: 62px; width: 818px; height: 47px;
    border-bottom: 1px solid var(--rule-grey);
  }
  .doc-title { position: absolute; left: 0; top: 11px; font-size: 13px; font-weight: 400; color: var(--text-grey); }
  .brand-name {
    position: absolute; right: 12px; top: 0; font-size: 27px; font-weight: 400;
    color: var(--brand-red); letter-spacing: 0.2px; line-height: 1.3;
  }

  .section-bar { position: absolute; left: 0; top: 166px; width: 281px; height: 12px; background: var(--brand-red); }
  .section-title {
    position: absolute; left: 310px; top: 163px; font-size: 14px; font-weight: 600;
    color: var(--heading-dark); letter-spacing: 0.3px;
  }

  .tips { list-style: none; }
  .tip { position: absolute; left: 165px; width: 710px; font-size: 15px; font-weight: 300; line-height: 21px; }
  .tip::before {
    content: ""; position: absolute; left: -67px; top: 3px; width: 11px; height: 11px;
    border-radius: 50%; background: var(--brand-red);
  }
  .tip strong { font-weight: 600; color: var(--text-grey); }

  .footer-band {
    position: absolute; left: 0; top: 926px; width: 927px; height: 154px;
    background: linear-gradient(90deg, var(--band-dark) 0%, #6a5550 30%, var(--band-mid) 55%, var(--band-red) 100%);
  }
  .page-number { position: absolute; left: 818px; top: 1122px; font-size: 16px; color: var(--brand-red); }
</style>
</head>
<body>
  <header class="page-header">
    <span class="doc-title">Website Performance Testing</span>
    <span class="brand-name">Veltrana</span>
  </header>

  <div class="section-bar"></div>
  <h2 class="section-title">DON’T</h2>

  <ul class="tips">
    <li class="tip" style="top:228px"><strong>Don’t</strong> ignore the dependency between page load times and user volume capacity. Measure both aspects at each stage of testing.</li>
    <li class="tip" style="top:328px"><strong>Don’t</strong> forget to process live web traffic logs to collect statistics on the types and volume of requests coming into your site so you can optimize load testing to reflect that reality.</li>
    <li class="tip" style="top:420px"><strong>Don’t</strong> run your load generation on the same cloud as your website to avoid contamination of test metrics.</li>
    <li class="tip" style="top:514px"><strong>Don’t</strong> assume that cloud testing is intrinsically less expensive than running on in-house infra­structure. In other words, keep your eye on the “meter.”</li>
    <li class="tip" style="top:605px; width:712px"><strong>Don’t</strong> rely on a single cloud vendor as vendors’ distinctive functional and operational characteristics may affect test results.</li>
  </ul>

  <div class="footer-band" role="img" aria-label="Photo of a laptop screen showing a performance line chart, tinted from dark grey to red"></div>

  <div class="page-number">5</div>
</body>
</html>
```